Food humor T-shirt and apparel company needs a Shopify site designed. We have logo files to help.

We are an apparel company based in Chicago by two cooking and food humor enthusiasts. We are looking for a redesign of our Shopify site. Our products are humorous quotes and pictures on shirts, sweaters and other apparel. The tagline for the company is - Find Your Yum. Wear Your Food. We want to see designs that incorporate our logo, brand color of royal purple, signify fun business casual clothing with amusing tags or images of trendy or esoteric food trends. The design should communicate excellence in taste but with maybe a satirical almost corporate type spin.
Target Market(s)
Hip, millennial foodies and cooks that love to try new foods, have great taste, and love to experiment in the restaurant or the kitchen.
Industry/Entity Type
Cooking
Look and feel
Each slider illustrates characteristics of the customer's brand and the style your logo design should communicate.

```html
<!DOCTYPE html>
<html lang="en">
<head>
<meta charset="utf-8">
<title>Tastiva — Find Your Yum. Wear Your Food.</title>
<link href="https://fonts.googleapis.com/css2?family=Raleway:wght@300;400;500;600;700&display=swap" rel="stylesheet">
<style>
:root{
  --purple:#7a1f7e;
  --royal:#0d3b96;
  --ink:#222;
  --muted:#555;
  --line:#cfcfcf;
  --band:#ececec;
  --white:#fff;
  --tee-black:#161616;
  --tee-white:#ececec;
  --tee-grey:#9c9c9c;
  --print-gold:#c9943e;
  --print-cookie:#9a6a3c;
  --print-red:#b8353a;
}
*{box-sizing:border-box;margin:0;padding:0}
html,body{width:1200px;height:3980px;overflow:hidden;background:var(--white);font-family:'Raleway',sans-serif;color:var(--ink)}
.page{position:relative;width:1200px;height:3980px}
.abs{position:absolute}
a{color:inherit;text-decoration:none}

/* header */
.social{display:flex;gap:20px}
.social span{width:19px;height:19px;border-radius:3px;background:#666;display:block}
.header-social{left:112px;top:45px}
.brand{font-weight:700;color:var(--purple);letter-spacing:1px}
.header-brand{left:0;width:1200px;top:72px;font-size:31px;display:flex;justify-content:center;align-items:center;gap:10px}
.brand-dot{width:12px;height:12px;border-radius:50%;background:var(--purple)}
.header-tools{right:112px;top:44px;display:flex;gap:18px;align-items:center;font-size:14px}
.header-rule{left:111px;width:977px;top:120px;height:1px;background:var(--line)}
.main-nav{left:0;width:1200px;top:137px;display:flex;justify-content:center;gap:42px;font-size:12.5px;font-weight:500;text-transform:uppercase}

/* hero */
.hero{left:0;top:167px;width:1200px;height:571px;
  background:
    radial-gradient(ellipse 210px 300px at 870px 360px,#f4f1ec 0%,#e9e3da 70%,transparent 100%),
    radial-gradient(ellipse 150px 130px at 880px 210px,#b0794f 0%,#8d5a37 60%,transparent 100%),
    radial-gradient(ellipse 220px 320px at 520px 300px,#f7f5f1 0%,#ece7df 70%,transparent 100%),
    radial-gradient(ellipse 120px 100px at 640px 130px,#c08b64 0%,#a46f48 60%,transparent 100%),
    radial-gradient(ellipse 180px 200px at 330px 520px,#3f5b85 0%,#2d4467 60%,transparent 100%),
    radial-gradient(ellipse 600px 90px at 600px 560px,#d9b98a 0%,transparent 100%),
    linear-gradient(180deg,#e6e7e6 0%,#dcdcda 55%,#c9a77c 85%,#b88a5c 100%);}
.hero-title{left:0;width:1200px;top:410px;text-align:center;font-size:46px;font-weight:400;color:#1c1c1c}
.btn{display:flex;align-items:center;justify-content:center;background:var(--purple);color:var(--white);font-weight:500}
.hero-btn{left:533px;top:506px;width:132px;height:44px;font-size:15px}
.chev{top:440px}

/* section titles */
.sec-title{left:0;width:1200px;text-align:center;font-size:31px;font-weight:400;letter-spacing:4px;text-transform:uppercase}
.orn{width:10px;height:10px;border-radius:50%;background:var(--purple)}

/* featured */
.card{width:235px;height:218px;border:1px solid var(--line);background:var(--white);overflow:hidden}
.art{position:absolute;inset:0}
.art-mug{background:
  radial-gradient(ellipse 22% 16% at 50% 62%,var(--print-cookie) 0%,#c9a27a 60%,transparent 100%),
  radial-gradient(ellipse 42% 36% at 48% 56%,#fbfbfb 0%,#e6e6e6 80%,transparent 100%),
  radial-gradient(ellipse 40% 8% at 50% 88%,#d5d5d5 0%,transparent 100%),#fff}
.art-mug-red{background:
  radial-gradient(ellipse 30% 6% at 50% 70%,var(--print-red) 0%,transparent 100%),
  radial-gradient(ellipse 42% 36% at 48% 56%,#fbfbfb 0%,#e3e3e3 80%,transparent 100%),
  radial-gradient(ellipse 40% 8% at 50% 88%,#d5d5d5 0%,transparent 100%),#fff}
.art-black{background:
  radial-gradient(circle at 50% 45%,var(--print-cookie) 0%,#7a4f2c 16%,transparent 18%),
  radial-gradient(ellipse 44% 48% at 50% 52%,var(--tee-black) 90%,transparent 100%),#fff}
.art-black-gold{background:
  radial-gradient(ellipse 12% 18% at 50% 50%,var(--print-gold) 0%,#a57428 60%,transparent 100%),
  radial-gradient(ellipse 44% 48% at 50% 52%,var(--tee-black) 90%,transparent 100%),#fff}
.art-white{background:
  radial-gradient(circle at 50% 48%,var(--print-cookie) 0%,#c79d6e 14%,transparent 16%),
  radial-gradient(ellipse 40% 48% at 50% 55%,var(--tee-white) 90%,transparent 100%),
  radial-gradient(ellipse 10% 10% at 50% 8%,#c9967a 0%,transparent 100%),#fff}
.art-white-waffle{background:
  radial-gradient(ellipse 18% 10% at 50% 50%,#d49a4a 0%,#e0b77c 60%,transparent 100%),
  radial-gradient(ellipse 46% 48% at 50% 52%,var(--tee-white) 90%,transparent 100%),#fff}
.art-grey{background:
  radial-gradient(ellipse 12% 18% at 50% 50%,#2a2a2a 0%,#555 60%,transparent 100%),
  radial-gradient(ellipse 44% 48% at 50% 52%,var(--tee-grey) 90%,transparent 100%),#fff}
.art-tank{background:
  radial-gradient(ellipse 10% 9% at 50% 55%,#9fc7a3 0%,#d7a0a8 60%,transparent 100%),
  radial-gradient(ellipse 28% 48% at 50% 52%,#2e2e2e 90%,transparent 100%),#fff}
.quick{position:absolute;left:56px;top:88px;width:125px;height:38px;background:var(--royal);color:#fff;font-size:16px;display:flex;align-items:center;justify-content:center}
.label{width:235px;text-align:center;font-size:17px;font-weight:500}
.price{width:235px;text-align:center;font-size:15px;color:var(--muted)}

/* steps */
.band{left:0;top:1732px;width:1200px;height:334px;background:var(--band)}
.step{width:272px;height:172px;background:var(--white);top:1814px}
.step-icon{width:79px;height:77px;top:1861px;display:flex;align-items:center;justify-content:center}
.step h3{position:absolute;left:66px;top:38px;font-size:30px;font-weight:500}
.step p{position:absolute;left:66px;top:84px;font-size:15px;line-height:22px;color:var(--muted);width:190px}

/* products */
.frame{border:1px solid var(--line);overflow:hidden;background:#fff}
.offer{background:var(--royal);color:#fff}
.offer h4{position:absolute;left:28px;top:24px;font-size:29px;font-weight:400}
.offer .amt{position:absolute;left:28px;top:70px;font-size:20px;font-weight:300}
.offer .ghost{position:absolute;left:30px;top:143px;width:135px;height:44px;border:1px solid #fff;font-size:17px;font-weight:300;display:flex;align-items:center;justify-content:center}

/* testimonials */
.quote{width:300px;font-size:15.5px;line-height:28px;color:#666}
.sig{font-size:15.5px;font-weight:600;display:flex;align-items:center;gap:14px}

/* instagram */
.insta{left:0;top:3159px;width:1200px;height:366px;display:grid;grid-template-columns:repeat(6,200px);grid-template-rows:repeat(2,183px)}
.insta div{width:200px;height:183px}

/* footer */
.foot-nav{font-size:12.5px;color:#444;display:flex;gap:14px}
.news-input{left:758px;top:3744px;width:338px;height:53px;border:1px solid var(--line);border-radius:27px;background:#f7f7f7}
.news-input .ph{position:absolute;left:46px;top:17px;font-size:14px;color:#555}
.news-input .send{position:absolute;right:4px;top:3px;width:114px;height:45px;border-radius:23px;font-size:18px}
.pay{left:0;width:1200px;top:3910px;display:flex;justify-content:center;gap:8px;font-size:11px;font-weight:700}
.pay span{padding:2px 6px;border:1px solid #bbb;color:#333}
.copy{left:0;width:1200px;top:3947px;text-align:center;font-size:12px;color:#333}
</style>
</head>
<body>
<div class="page">

  <header>
    <div class="abs social header-social"><span></span><span></span><span></span><span></span><span></span></div>
    <div class="abs header-brand brand"><i class="brand-dot"></i>Tastiva</div>
    <div class="abs header-tools">
      <svg width="16" height="16" viewBox="0 0 16 16"><circle cx="6.5" cy="6.5" r="5" fill="none" stroke="#111" stroke-width="2"/><line x1="10" y1="10" x2="15" y2="15" stroke="#111" stroke-width="2.5"/></svg>
      <svg width="16" height="17" viewBox="0 0 16 17"><rect x="1" y="5" width="14" height="11" fill="none" stroke="#111" stroke-width="2"/><path d="M5 5V3a3 3 0 0 1 6 0v2" fill="none" stroke="#111" stroke-width="2"/></svg>
      <svg width="16" height="16" viewBox="0 0 16 16"><circle cx="8" cy="5" r="4" fill="#111"/><path d="M0 16a8 6 0 0 1 16 0z" fill="#111"/></svg>
      <span>USD ▾</span>
    </div>
    <div class="abs header-rule"></div>
    <nav class="abs main-nav">
      <a>Home</a><a>About Us</a><a>Apparel Printing</a><a>Products</a><a>Categories</a><a>Print Shop</a><a>Blog</a><a>Contact Us</a>
    </nav>
  </header>

  <section>
    <div class="abs hero" role="img" aria-label="Photo of a laughing couple in a bright white-tiled kitchen, both wearing white tees with waffle and ice cream food-pun prints"></div>
    <svg class="abs chev" style="left:48px" width="16" height="24" viewBox="0 0 16 24"><path d="M13 2 3 12l10 10" fill="none" stroke="#222" stroke-width="3"/></svg>
    <svg class="abs chev" style="right:48px" width="16" height="24" viewBox="0 0 16 24"><path d="M3 2l10 10L3 22" fill="none" stroke="#fff" stroke-width="3"/></svg>
    <h1 class="abs hero-title">Find Your Yum. Wear Your Food</h1>
    <a class="abs btn hero-btn">Shop Now</a>
  </section>

  <section>
    <div class="abs orn" style="left:595px;top:798px"></div>
    <h2 class="abs sec-title" style="top:830px">Featured Collection</h2>

    <div class="abs card" style="left:111px;top:895px"><div class="art art-mug-red" role="img" aria-label="White mug with a waffles over pancakes pun print"></div><div class="quick">Quick View</div></div>
    <div class="abs card" style="left:358px;top:895px"><div class="art art-black" role="img" aria-label="Black tee with a round cookie pun print"></div></div>
    <div class="abs card" style="left:607px;top:895px"><div class="art art-mug" role="img" aria-label="White mug with a cookie pun print"></div></div>
    <div class="abs card" style="left:854px;top:895px"><div class="art art-tank" role="img" aria-label="Black tank top with an ice cream heart print"></div></div>
    <div class="abs label" style="left:111px;top:1128px">Lorem ipsum dolor sit ame</div>
    <div class="abs price" style="left:111px;top:1154px">₹ 1,788.00</div>
    <div class="abs label" style="left:358px;top:1128px">Lorem ipsum dolor</div>
    <div class="abs label" style="left:607px;top:1128px">Lorem ipsum dolor</div>
    <div class="abs label" style="left:854px;top:1128px">Lorem ipsum dolor</div>

    <div class="abs card" style="left:111px;top:1229px"><div class="art art-black-gold" role="img" aria-label="Black tee with a gold cobbler pun print"></div></div>
    <div class="abs card" style="left:358px;top:1229px"><div class="art art-white" role="img" aria-label="Model in a white tee with a cookie print"></div></div>
    <div class="abs card" style="left:607px;top:1229px"><div class="art art-white-waffle" role="img" aria-label="White tee with a waffles over pancakes print"></div></div>
    <div class="abs card" style="left:854px;top:1229px"><div class="art art-grey" role="img" aria-label="Grey tee with a dark cobbler pun print"></div></div>
    <div class="abs label" style="left:111px;top:1461px">Lorem ipsum dolor</div>
    <div class="abs label" style="left:358px;top:1461px">Lorem ipsum dolor</div>
    <div class="abs label" style="left:607px;top:1461px">Lorem ipsum dolor</div>
    <div class="abs label" style="left:854px;top:1461px">Lorem ipsum dolor</div>

    <a class="abs btn" style="left:527px;top:1559px;width:146px;height:47px;font-size:17px">Shop Now</a>
  </section>

  <section>
    <div class="abs band"></div>
    <div class="abs step" style="left:153px"><h3>Choose...</h3><p>Lorem ipsum dolor sit amet, consectetur</p></div>
    <div class="abs step-icon" style="left:111px;background:var(--purple)">
      <svg width="40" height="38" viewBox="0 0 40 38"><path d="M13 3 3 9l4 8 4-2v20h18V15l4 2 4-8-10-6a7 5 0 0 1-14 0z" fill="none" stroke="#fff" stroke-width="2.5" stroke-linejoin="round"/></svg>
    </div>
    <div class="abs step" style="left:485px"><h3>Create...</h3><p>Lorem ipsum dolor sit amet, consectetur</p></div>
    <div class="abs step-icon" style="left:443px;background:var(--royal)">
      <svg width="42" height="42" viewBox="0 0 42 42"><circle cx="21" cy="21" r="18" fill="none" stroke="#fff" stroke-width="4"/><circle cx="21" cy="21" r="6" fill="none" stroke="#fff" stroke-width="3"/></svg>
    </div>
    <div class="abs step" style="left:816px"><h3>Checkout...</h3><p>Lorem ipsum dolor sit amet, consectetur</p></div>
    <div class="abs step-icon" style="left:774px;background:var(--purple)">
      <svg width="40" height="38" viewBox="0 0 40 38"><rect x="4" y="12" width="32" height="8" fill="none" stroke="#fff" stroke-width="2.5"/><rect x="7" y="20" width="26" height="16" fill="none" stroke="#fff" stroke-width="2.5"/><line x1="20" y1="12" x2="20" y2="36" stroke="#fff" stroke-width="2.5"/><path d="M20 12c-4-8-12-6-8 0M20 12c4-8 12-6 8 0" fill="none" stroke="#fff" stroke-width="2.5"/></svg>
    </div>
  </section>

  <section>
    <div class="abs orn" style="left:595px;top:2132px"></div>
    <h2 class="abs sec-title" style="top:2156px">Products</h2>

    <div class="abs frame" style="left:111px;top:2216px;width:562px;height:231px"></div>
    <div class="abs" style="left:150px;top:2222px;width:200px;height:218px;background:
      radial-gradient(ellipse 12% 10% at 50% 55%,#9fc7a3 0%,#d7a0a8 60%,transparent 100%),
      radial-gradient(ellipse 30% 48% at 50% 52%,#2e2e2e 90%,transparent 100%)" role="img" aria-label="Black tank top with an ice cream heart print"></div>
    <div class="abs offer" style="left:383px;top:2223px;width:281px;height:217px">
      <h4>Get <b>10%</b> Off</h4>
      <div class="amt">$41.00</div>
      <a class="ghost">Shop Now</a>
    </div>
    <div class="abs frame" style="left:111px;top:2467px;width:269px;height:241px;background:
      radial-gradient(ellipse 10% 9% at 50% 68%,var(--print-gold) 0%,transparent 100%),
      radial-gradient(ellipse 36% 45% at 50% 78%,#1c1816 88%,transparent 100%),
      radial-gradient(ellipse 48% 55% at 50% 82%,#5a4034 90%,transparent 100%),
      radial-gradient(ellipse 14% 14% at 50% 14%,#e0b497 0%,transparent 100%),#f6f4f2" role="img" aria-label="Smiling woman wearing a black apron with a cobbler pun print"></div>
    <div class="abs frame" style="left:397px;top:2467px;width:275px;height:241px;background:
      radial-gradient(circle at 52% 55%,var(--print-cookie) 0%,#c79d6e 12%,transparent 14%),
      radial-gradient(ellipse 40% 52% at 50% 66%,var(--tee-white) 90%,transparent 100%),
      radial-gradient(ellipse 12% 14% at 50% 12%,#d2a184 0%,transparent 100%),#fafafa" role="img" aria-label="Man wearing a white tee with a cookie print"></div>
    <div class="abs frame" style="left:689px;top:2216px;width:399px;height:492px;background:
      radial-gradient(ellipse 14% 16% at 52% 44%,var(--print-gold) 0%,#a57428 60%,transparent 100%),
      radial-gradient(ellipse 46% 58% at 50% 70%,var(--tee-black) 92%,transparent 100%),
      radial-gradient(ellipse 12% 12% at 50% 10%,#cf9f80 0%,transparent 100%),#f6f6f6" role="img" aria-label="Man wearing a black tee with a gold cobbler pun print"></div>
  </section>

  <section>
    <div class="abs orn" style="left:240px;top:2765px"></div>
    <h2 class="abs" style="left:113px;top:2800px;font-size:31px;font-weight:400;letter-spacing:4px">TESTIMONIALS</h2>

    <p class="abs quote" style="left:122px;top:2870px">Sed ut perspiciatis unde omnis iste natus error sit voluptatem accusantiumremque laudantium, totam rem aperiam,</p>
    <div class="abs sig" style="left:234px;top:2975px"><svg width="66" height="10" viewBox="0 0 66 10"><path d="M1 3q8 8 16 0t16 0 16 0 16 0" fill="none" stroke="#7a1f7e" stroke-width="2.5"/></svg>-Mara Quill</div>

    <p class="abs quote" style="left:459px;top:2870px">Sed ut perspiciatis unde omnis iste natus error sit voluptatem accusantiumremque laudantium, totam rem aperiam,</p>
    <div class="abs sig" style="left:571px;top:2975px"><svg width="66" height="10" viewBox="0 0 66 10"><path d="M1 3q8 8 16 0t16 0 16 0 16 0" fill="none" stroke="#7a1f7e" stroke-width="2.5"/></svg>-Mara Quill</div>

    <p class="abs quote" style="left:795px;top:2870px">Sed ut perspiciatis unde omnis iste natus error sit voluptatem accusantiumremque laudantium, totam rem aperiam,</p>
    <div class="abs sig" style="left:907px;top:2975px"><svg width="66" height="10" viewBox="0 0 66 10"><path d="M1 3q8 8 16 0t16 0 16 0 16 0" fill="none" stroke="#7a1f7e" stroke-width="2.5"/></svg>-Mara Quill</div>
  </section>

  <section>
    <div class="abs orn" style="left:595px;top:3074px"></div>
    <h2 class="abs sec-title" style="top:3100px">Instagram</h2>
    <a class="abs btn" style="left:960px;top:3083px;width:128px;height:39px;font-size:15px">Follow Us</a>
    <div class="abs insta">
      <div style="background:radial-gradient(ellipse 32% 30% at 40% 45%,#d8323c 0%,#9c1f27 70%,transparent 100%),radial-gradient(circle at 40% 45%,#5a5a5e 0%,#2e2e32 70%)" role="img" aria-label="Heart-shaped steak on a dark slate board"></div>
      <div style="background:radial-gradient(ellipse 40% 50% at 35% 50%,#f3e6cf 0%,transparent 100%),radial-gradient(ellipse 35% 50% at 75% 55%,#4a3a33 0%,transparent 100%),#d8d2c8" role="img" aria-label="Couple laughing while cooking together"></div>
      <div style="background:radial-gradient(ellipse 30% 45% at 70% 40%,#b8322c 0%,transparent 100%),radial-gradient(ellipse 40% 55% at 30% 55%,#d7b7a0 0%,transparent 100%),#4a3a36" role="img" aria-label="Couple snacking by an open fridge"></div>
      <div style="background:radial-gradient(circle at 30% 35%,#e6c7a0 0 12%,transparent 14%),radial-gradient(circle at 70% 65%,#7a3a2a 0 12%,transparent 14%),radial-gradient(circle at 60% 25%,#b13a3a 0 8%,transparent 10%),linear-gradient(135deg,#b98f6a,#5e4030)" role="img" aria-label="Table spread of pastries, chocolates and berries"></div>
      <div style="background:radial-gradient(ellipse 50% 30% at 50% 85%,#f2f1ec 0%,transparent 100%),linear-gradient(180deg,#98b27c 0%,#d8e0cc 55%,#f4f2ee 100%)" role="img" aria-label="Couple having breakfast outdoors"></div>
      <div style="background:radial-gradient(circle at 30% 35%,#e9b85a 0 10%,transparent 12%),radial-gradient(circle at 70% 70%,#e9b85a 0 10%,transparent 12%),linear-gradient(135deg,#b03220,#7a1e14)" role="img" aria-label="Pepperoni pizza slices close up"></div>
      <div style="background:radial-gradient(ellipse 40% 30% at 60% 80%,#c43d2e 0%,transparent 100%),radial-gradient(ellipse 40% 50% at 30% 40%,#d8b79e 0%,transparent 100%),#6b5448" role="img" aria-label="Couple cooking vegetables at the stove"></div>
      <div style="background:radial-gradient(ellipse 30% 30% at 50% 50%,#2a3f7a 0%,#c8283a 60%,transparent 100%),#f7f7f7" role="img" aria-label="Heart of blueberries and strawberries on white"></div>
      <div style="background:radial-gradient(circle at 50% 50%,#a8502a 0 14%,#f4ece4 16% 24%,transparent 26%),radial-gradient(ellipse 50% 50% at 50% 55%,#e4b89c 0%,transparent 100%),#d6cfc8" role="img" aria-label="Hands holding a cup of tea"></div>
      <div style="background:radial-gradient(circle at 50% 50%,#c7344a 0 10%,#d4a060 12% 22%,#1e2a2e 24% 44%,transparent 46%),#252a2e" role="img" aria-label="Waffles with berries on a dark plate"></div>
      <div style="background:radial-gradient(ellipse 18% 16% at 32% 70%,#fff 90%,transparent 100%),radial-gradient(ellipse 18% 16% at 70% 70%,#fff 90%,transparent 100%),radial-gradient(circle at 52% 78%,#d42b3a 0 4%,transparent 5%),linear-gradient(180deg,#a9c8e8 0%,#bcd4ec 60%,#ece6da 100%)" role="img" aria-label="Two white mugs with strawberries on a sunny table"></div>
      <div style="background:radial-gradient(ellipse 40% 40% at 45% 35%,#f2d28e 0%,transparent 100%),radial-gradient(ellipse 40% 35% at 70% 80%,#c2955e 0%,transparent 100%),#eee8e2" role="img" aria-label="Woman enjoying breakfast in bed"></div>
    </div>
  </section>

  <footer>
    <div class="abs brand" style="left:111px;top:3665px;font-size:31px;display:flex;align-items:center;gap:10px"><i class="brand-dot"></i>Tastiva</div>
    <div class="abs foot-nav" style="left:111px;top:3733px"><a>HOME</a>|<a>ABOUT US</a>|<a>APPAREL PRINTING</a>|<a>PRODUCTS</a></div>
    <div class="abs foot-nav" style="left:111px;top:3758px"><a>CATEGORIES</a>|<a>PRINT SHOP</a>|<a>BLOG</a>|<a>CONTACT US</a></div>
    <div class="abs social" style="left:111px;top:3818px"><span></span><span></span><span></span><span></span><span></span></div>

    <h2 class="abs" style="left:757px;top:3643px;font-size:29px;font-weight:400;letter-spacing:4px">NEWSLETTER</h2>
    <div class="abs" style="left:758px;top:3691px;font-size:13.5px;letter-spacing:2.5px;font-weight:500">GET IN TOUCH WITH US TODAY</div>
    <div class="abs news-input">
      <svg class="abs" style="left:16px;top:18px" width="22" height="16" viewBox="0 0 22 16"><rect x="1" y="1" width="20" height="14" fill="none" stroke="#666" stroke-width="1.5"/><path d="M1 1l10 8 10-8" fill="none" stroke="#666" stroke-width="1.5"/></svg>
      <span class="ph">Enter Your Email Address</span>
      <a class="btn send">Send</a>
    </div>

    <div class="abs pay"><span>Paylo</span><span>Cardix</span><span>Mondo</span><span>Amexo</span></div>
    <div class="abs copy">© Copyrights 2019 The Company name All Rights Reserved</div>
  </footer>

</div>
</body>
</html>
```